Bright Wave Labs

We need a professional letter head format for our company. Now we have a logo but need to desing a new logo also. I have uploaded our old logo. Use the color in the logo and design a new one.

Dear Designers , Need to mention "BWL" and please dont use our old LOGO. we need a new catchy one.

```html
<!DOCTYPE html>
<html lang="en">
<head>
<meta charset="utf-8">
<title>Bright Wave Labs — Letterhead</title>
<link href="https://fonts.googleapis.com/css2?family=Open+Sans:wght@400;600;700&family=Arimo:wght@700&display=swap" rel="stylesheet">
<style>
  :root {
    --bg: #ececec;
    --paper: #ffffff;
    --navy: #0f2d4c;
    --green: #8dc63f;
    --ink: #2a2a2a;
    --muted: #4a4a4a;
    --ghost: #f1f5f8;
  }
  * { box-sizing: border-box; margin: 0; padding: 0; }
  html, body { width: 1200px; height: 1120px; overflow: hidden; background: var(--bg); }
  .canvas { position: relative; width: 1200px; height: 1120px; }
  .letterhead {
    position: absolute; left: 218px; top: 22px;
    width: 764px; height: 1076px;
    background: var(--paper);
    box-shadow: 0 6px 24px rgba(0,0,0,0.12);
    overflow: hidden;
    font-family: "Open Sans", Arial, sans-serif;
    color: var(--ink);
  }
  .top-rule { position: absolute; left: 0; top: 0; width: 470px; height: 6px; background: var(--green); }
  .top-rule-dark { position: absolute; left: 0; top: 6px; width: 60px; height: 2px; background: #1a1a1a; }
  .brand { position: absolute; left: 64px; top: 74px; display: flex; align-items: center; gap: 10px; }
  .brand-dot { width: 26px; height: 26px; border-radius: 50%; background: var(--green); }
  .brand-name { font-weight: 700; font-size: 17px; color: var(--navy); letter-spacing: 0.5px; }
  .ghost-mark {
    position: absolute; left: 0; right: 0; top: 470px; text-align: center;
    font-weight: 700; font-size: 64px; color: var(--ghost); letter-spacing: 2px;
  }
  .letter-body { position: absolute; left: 64px; top: 210px; width: 580px; }
  .salutation { font-family: "Arimo", Arial, sans-serif; font-weight: 700; font-size: 17px; margin-bottom: 14px; }
  .letter-body p { font-size: 12.5px; line-height: 1.55; color: var(--muted); margin-bottom: 22px; }
  .signature { width: 150px; height: 70px; margin-top: 26px; background: linear-gradient(90deg, #e6e6e6, #f4f4f4); border-radius: 4px; }
  .contact { position: absolute; right: 40px; bottom: 150px; text-align: right; font-size: 11px; line-height: 1.7; color: var(--ink); }
  .contact .row { display: flex; justify-content: flex-end; align-items: center; gap: 6px; }
  .contact svg { width: 11px; height: 11px; fill: var(--navy); }
  .footer-wave { position: absolute; left: 0; bottom: 0; width: 764px; height: 170px; }
</style>
</head>
<body>
<div class="canvas">
  <div class="letterhead">
    <div class="top-rule"></div>
    <div class="top-rule-dark"></div>

    <div class="brand">
      <span class="brand-dot"></span>
      <span class="brand-name">BRIGHT WAVE LABS</span>
    </div>

    <div class="ghost-mark" aria-hidden="true">BWL</div>

    <main class="letter-body">
      <div class="salutation">Dear Mr. John,</div>
      <p>Lorem Ipsum is simply dummy text of the printing and typesetting industry. Lorem Ipsum has been the industry's standard dummy text ever since the 1500s, when an unknown printer took a galley of type and scrambled it to make a type specimen book. It has survived not only five centuries, but also the leap into electronic typesetting remaining essentially unchanged.</p>
      <p>The standard chunk of Lorem Ipsum used since the 1500s is reproduced below for those interested. Sections 1.10.32 and 1.10.33 from "de Finibus Bonorum et Malorum" by Aurelian Vesk are also reproduced in their exact original form, accompanied by English versions from the 1914 translation by H. Marlowe.</p>
      <p>Lorem Ipsum is simply dummy text of the printing and typesetting industry. Lorem Ipsum has been the industry's standard dummy text ever since the 1500s, when an unknown printer took a galley of type and scrambled it to make a type specimen book. It has survived not only five centuries, but also the leap into electronic typesetting, remaining essentially unchanged. It was popularised in the</p>
      <div class="signature" role="img" aria-label="Handwritten signature of the sender"></div>
    </main>

    <div class="contact">
      <div class="row">
        <svg viewBox="0 0 24 24"><path d="M6.6 10.8a15 15 0 006.6 6.6l2.2-2.2a1 1 0 011-.25 11.4 11.4 0 003.6.57 1 1 0 011 1V20a1 1 0 01-1 1A17 17 0 013 4a1 1 0 011-1h3.5a1 1 0 011 1c0 1.25.2 2.45.57 3.6a1 1 0 01-.25 1z"/></svg>
        <span>(+945)210-774-362</span>
        <svg viewBox="0 0 24 24"><path d="M2 5h20v14H2z M2 5l10 8 10-8" fill="none" stroke="#0f2d4c" stroke-width="2"/></svg>
        <span>hello@brightwavelabs.com</span>
        <span style="margin-left:14px">www.brightwavelabs.com</span>
      </div>
      <div>Po. box 201, Street Name, City Name, Zip Code 00000</div>
    </div>

    <svg class="footer-wave" viewBox="0 0 764 170" preserveAspectRatio="none" aria-hidden="true">
      <path d="M0 170 L764 170 L764 20 C650 110 420 158 0 168 Z" fill="var(--navy)"/>
      <path d="M0 158 C400 150 620 100 764 4" fill="none" stroke="var(--green)" stroke-width="7"/>
    </svg>
  </div>
</div>
</body>
</html>
```